Tree Service Billboard 20x8 ft

We need a billboard design for a tree service company.
The billboard is 20ft x 8 ft so we need a design that is capable to stretching to those dimensions without loosing quality.
I have attached a series of images.
Image 1- Simply a billboard that I think looks good that I would like you to use for inspiration. I am aiming for the same format only no color in the wording, just black white, or gray. I like the the trees in the background, the logo placed to the left, and wording on the right.
Image 2- Current Logo I would like to the left of the billboard
Image 3- Another format of current logo if needed.
Image 4- A drawn out design template
Image 5- Another drawn out design template

Specific things I am looking for
-The contact number to be the largest thing on the design
-The logo on the design
-Key points to the design to say:
Tree Removal
Tree Trimming
Land Development
Stump Grinding
Storm Response
Insured
Free Bids
-The facebook logo
-The Google Logo

```html
<!DOCTYPE html>
<html lang="en">
<head>
<meta charset="UTF-8">
<title>Ridgeway Tree Service Billboard</title>
<link rel="stylesheet" href="https://fonts.googleapis.com/css2?family=Teko:wght@600&family=Orbitron:wght@800&display=swap">
<style>
  :root {
    --white: #ffffff;
    --black: #000000;
    --gray: #6b6b6b;
    --phone-gray: #8a8a8a;
    --forest-dark: #1f4a26;
    --forest-mid: #3f7a45;
    --haze: #9cc3a2;
  }
  html, body {
    margin: 0;
    padding: 0;
    width: 1200px;
    height: 655px;
    overflow: hidden;
    background: var(--white);
  }
  .billboard {
    position: absolute;
    left: 54px;
    top: 109px;
    width: 1091px;
    height: 436px;
    overflow: hidden;
  }
  .forest-backdrop {
    position: absolute;
    inset: 0 0 72px 0;
    background: linear-gradient(180deg, var(--haze) 0%, var(--forest-mid) 35%, var(--forest-dark) 100%);
  }
  .contact-band {
    position: absolute;
    left: 0;
    right: 0;
    bottom: 0;
    height: 72px;
    background: var(--black);
    border-top: 2px solid var(--gray);
    box-sizing: border-box;
  }
  .phone {
    position: absolute;
    left: 0;
    width: 1092px;
    top: 12px;
    text-align: center;
    font-family: "Orbitron", sans-serif;
    font-weight: 800;
    font-size: 40px;
    line-height: 1.1;
    letter-spacing: 8px;
    color: var(--phone-gray);
  }
  .social {
    position: absolute;
    top: 10px;
    width: 49px;
    height: 49px;
    border: 3px solid var(--phone-gray);
    border-radius: 50%;
    box-sizing: border-box;
  }
  .social--one { left: 894px; }
  .social--two { left: 968px; }

  .service {
    position: absolute;
    height: 59px;
    padding: 8px 14px 0;
    box-sizing: border-box;
    display: flex;
    align-items: center;
    justify-content: center;
    font-family: "Teko", sans-serif;
    font-weight: 600;
    font-size: 50px;
    line-height: 1;
    color: var(--white);
    text-transform: uppercase;
    white-space: nowrap;
  }
  .service--dark { background: var(--black); }
  .service--gray { background: var(--gray); }

  .service--removal   { left: 22px;  top: 39px; }
  .service--trimming  { left: 96px;  top: 106px; }
  .service--stump     { left: 22px;  top: 175px; }
  .service--insured   { left: 51px;  top: 246px; }
  .service--land      { right: 25px; top: 39px; }
  .service--bids      { right: 95px; top: 106px; }
  .service--storm     { right: 33px; top: 175px; }

  .logo-badge {
    position: absolute;
    left: 412px;
    top: 14px;
    width: 268px;
    height: 268px;
  }
  .company-name {
    position: absolute;
    left: 0;
    width: 1092px;
    top: 300px;
    text-align: center;
    font-family: "Teko", sans-serif;
    font-weight: 600;
    font-size: 58px;
    line-height: 1;
    color: var(--white);
    text-transform: uppercase;
    white-space: nowrap;
    transform: scaleY(1.35);
    transform-origin: top center;
  }
</style>
</head>
<body>
  <div class="billboard">
    <div class="forest-backdrop" role="img" aria-label="Photo of forested green mountain ridges under a hazy sky"></div>

    <div class="service service--dark service--removal">Tree Removal</div>
    <div class="service service--gray service--trimming">Tree Trimming</div>
    <div class="service service--dark service--stump">Stump Grinding</div>
    <div class="service service--gray service--insured">Insured</div>

    <div class="service service--dark service--land">Land Development</div>
    <div class="service service--gray service--bids">Free Bids</div>
    <div class="service service--dark service--storm">Storm Response</div>

    <svg class="logo-badge" viewBox="0 0 268 268">
      <circle cx="134" cy="134" r="134" fill="#ffffff"/>
      <circle cx="134" cy="134" r="122" fill="#000000"/>
      <circle cx="134" cy="134" r="114" fill="#6b6b6b"/>
      <circle cx="134" cy="134" r="108" fill="#ffffff"/>
      <circle cx="134" cy="134" r="104" fill="#d8d8d8" role="img" aria-label="Company emblem: silhouette of a large tree with a climber on its trunk"/>
    </svg>

    <div class="company-name">Ridgeway Tree Service</div>

    <div class="contact-band">
      <div class="phone">417-555-0148</div>
      <div class="social social--one"></div>
      <div class="social social--two"></div>
    </div>
  </div>
</body>
</html>
```